Poster design for "A Frame" Sign

I need a design for an A Frame sign. Measurements and Specifications here:
http://www.trimboxdepot.com.au/pg/a-boards/ABPBBLKPRT-Print-Specs.pdf

Actually, it will need to be two designs, one with an arrow pointing left and one with an arrow pointing right, otherwise exactly the same.

LOGO to be used is attached. Colours of design should match logo and should also include orange tones.

The A Frame sign is to be put on the driveway of my home studio at a main road in a residential suburban area. Cars drive by at around 50 km/h, so there needs to be an eye catcher that there is a nurturing home massage studio here.

Logo can be left or right, somehow incorporated into the text below:
-
[Big header, ideally "LeHavre" font]
Sorela Healing
Massage Studio

[slightly smaller font, serif, with bullet points]
- Relaxation Massage
- Remedial Massage
- Pregnancy Massage
- Kahuna Massage

[big Arrow to the left/right - one for each side of the frame]

[sans serif font, same size as above]
Bookings essential!
ph 0491 578 264
www.sorelahealing.com.au

[serif font, same as above]
EFTPOS and instant health fund claims available.
-

Residential

f37022

```html
<!DOCTYPE html>
<html lang="en">
<head>
<meta charset="utf-8">
<title>Sorela Healing Massage – A-Frame Sign</title>
<link href="https://fonts.googleapis.com/css2?family=Original+Surfer&family=Quicksand:wght@500;700&family=Montserrat:wght@600;700&display=swap" rel="stylesheet">
<style>
  :root {
    --maroon: #8b1a3f;
    --pink: #de1f5e;
    --pink-soft: #f0518f;
    --white: #ffffff;
    --bg-light: #fbfbfb;
    --bg-edge: #d9d9d9;
  }
  * { margin: 0; padding: 0; box-sizing: border-box; }
  html, body { width: 810px; height: 1200px; overflow: hidden; }
  body { background: var(--bg-edge); }
  .sign {
    position: relative;
    width: 810px;
    height: 1200px;
    overflow: hidden;
    background: radial-gradient(ellipse at 50% 45%, var(--bg-light) 0%, #eeeeee 55%, var(--bg-edge) 100%);
    font-family: "Quicksand", sans-serif;
  }
  .brand-mark {
    position: absolute;
    left: 252px;
    top: 52px;
    width: 306px;
    height: 306px;
    border-radius: 50%;
    background: var(--pink);
    display: flex;
    align-items: center;
    justify-content: center;
  }
  .brand-mark span {
    font-family: "Original Surfer", sans-serif;
    color: var(--white);
    font-size: 40px;
    letter-spacing: 2px;
  }
  .headline {
    position: absolute;
    left: 0;
    right: 0;
    top: 382px;
    text-align: center;
    font-family: "Original Surfer", sans-serif;
    color: var(--maroon);
    font-size: 76px;
    line-height: 76px;
    letter-spacing: 4px;
    text-transform: uppercase;
  }
  .services {
    position: absolute;
    left: 0;
    right: 0;
    top: 560px;
    list-style: none;
    text-align: center;
    color: var(--pink);
    font-size: 36px;
    line-height: 42px;
    font-weight: 500;
    letter-spacing: 1px;
  }
  .booking-arrow {
    position: absolute;
    left: 118px;
    top: 789px;
    width: 624px;
    height: 144px;
  }
  .booking-arrow svg { position: absolute; inset: 0; }
  .booking-arrow .phone {
    position: absolute;
    left: 0;
    width: 590px;
    top: 12px;
    text-align: center;
    font-family: "Montserrat", sans-serif;
    font-weight: 700;
    color: var(--white);
    font-size: 68px;
    line-height: 80px;
    letter-spacing: 1px;
  }
  .booking-arrow .note {
    position: absolute;
    left: 0;
    width: 590px;
    top: 90px;
    text-align: center;
    color: var(--white);
    font-size: 27px;
    font-weight: 500;
    letter-spacing: 3px;
  }
  .website {
    position: absolute;
    left: 0;
    right: 0;
    top: 976px;
    text-align: center;
    color: var(--maroon);
    font-size: 36px;
    font-weight: 500;
    letter-spacing: 3px;
  }
  .payment {
    position: absolute;
    left: 0;
    right: 0;
    top: 1020px;
    text-align: center;
    color: var(--maroon);
    font-size: 21px;
    font-weight: 500;
  }
  .waves {
    position: absolute;
    left: 0;
    bottom: 0;
    width: 810px;
    height: 140px;
  }
</style>
</head>
<body>
  <main class="sign">
    <div class="brand-mark"><span>Sorela</span></div>

    <h1 class="headline">Sorela Healing<br>Massage</h1>

    <ul class="services">
      <li>Relaxation Massage</li>
      <li>Remedial Massage</li>
      <li>Pregnancy Massage</li>
      <li>Kahuna Massage</li>
    </ul>

    <div class="booking-arrow">
      <svg width="624" height="144" viewBox="0 0 624 144">
        <polygon points="0,0 590,0 624,72 590,144 0,144" fill="var(--pink)"/>
      </svg>
      <div class="phone">0491 578 264</div>
      <div class="note">Bookings essential!</div>
    </div>

    <p class="website">www.sorelahealing.com.au</p>
    <p class="payment">EFTPOS and instant health fund claims available.</p>

    <svg class="waves" viewBox="0 0 810 140" preserveAspectRatio="none">
      <path d="M0,20 C220,70 520,70 810,10 L810,140 L0,140 Z" fill="var(--pink-soft)"/>
      <path d="M0,38 C240,88 520,88 810,36 L810,140 L0,140 Z" fill="var(--white)"/>
      <path d="M0,60 C260,110 540,110 810,62 L810,140 L0,140 Z" fill="var(--maroon)"/>
      <path d="M0,100 C300,130 560,120 810,92 L810,140 L0,140 Z" fill="var(--pink)"/>
    </svg>
  </main>
</body>
</html>
```